Coffeeshop menu for filter tip

We want to have a cannabis (coffeeshop) menu in the size 25mm wide x 60mm wide. Some examples attached.

it must have the following text:
Menu

WEED p/g
Oblivane €16
Cloudplum €14
Tide Runner €14
Quincefig €16
Mega Marsh €14
Grey Heron €14

HASH p/g
Tashar Amber €12
Pebble Frost€11
Lime Dunes €14
Ash Petal €10

Target Market(s)

tourist in Amsterdam

Requirements
Nice to have
• cannabis sign leaf
• No Cigarettes allowed symbol

```html
<!DOCTYPE html>
<html lang="en">
<head>
<meta charset="utf-8">
<title>Coffeeshop Menu</title>
<link rel="stylesheet" href="https://fonts.googleapis.com/css2?family=Questrial&display=swap">
<style>
  :root {
    --bg: #161616;
    --bg-soft: #232323;
    --panel: #000000;
    --yellow: #fbf35a;
    --white: #ffffff;
    --muted: #9a9a9a;
    --skyline: #0a0a0a;
  }
  html, body {
    margin: 0;
    padding: 0;
    width: 1200px;
    height: 2880px;
    overflow: hidden;
    background: var(--bg);
  }
  .menu {
    position: relative;
    width: 1200px;
    height: 2880px;
    overflow: hidden;
    background: var(--bg);
    font-family: "Questrial", sans-serif;
    color: var(--yellow);
  }
  .leaf-decor {
    position: absolute;
    border-radius: 50%;
  }
  .leaf-decor--top {
    left: 560px; top: -160px; width: 700px; height: 560px;
    background: radial-gradient(closest-side, #222 0%, rgba(34,34,34,0) 100%);
  }
  .leaf-decor--left {
    left: -260px; top: 700px; width: 640px; height: 900px;
    background: radial-gradient(closest-side, #252525 0%, rgba(37,37,37,0) 100%);
  }
  .leaf-decor--right {
    left: 820px; top: 1500px; width: 620px; height: 1000px;
    background: radial-gradient(closest-side, #262626 0%, rgba(38,38,38,0) 100%);
  }
  .notice {
    position: absolute;
    left: 216px; top: 46px;
    display: flex; align-items: center; gap: 28px;
    color: var(--white);
    font-size: 60px;
    letter-spacing: 17px;
    line-height: 1;
  }
  .notice svg { width: 70px; height: 70px; }
  .heading {
    position: absolute;
    display: flex; justify-content: space-between;
    font-size: 128px;
    line-height: 1;
    color: var(--yellow);
  }
  .heading--weed { left: 224px; width: 712px; top: 168px; }
  .heading--hash { left: 314px; width: 676px; top: 1522px; }
  .unit {
    position: absolute;
    color: var(--muted);
    font-size: 64px;
    line-height: 1;
  }
  .panel { position: absolute; background: var(--panel); }
  .panel--weed { left: 163px; top: 315px; width: 1037px; height: 1122px; }
  .tab--weed { position: absolute; left: 1040px; top: 184px; width: 160px; height: 140px; background: var(--panel); }
  .unit--weed { left: 1062px; top: 254px; }
  .tab--hash { position: absolute; left: 0; top: 1528px; width: 270px; height: 130px; }
  .panel--hash { left: 0; top: 1656px; width: 1048px; height: 768px; }
  .unit--hash { left: 54px; top: 1600px; }
  .price-list { position: absolute; margin: 0; padding: 0; list-style: none; }
  .price-list li {
    display: flex; align-items: center;
    height: 176px;
    font-size: 100px;
    line-height: 1;
  }
  .price-list .name { text-transform: uppercase; color: var(--yellow); }
  .price-list .price { color: var(--white); }
  .price-list--weed { left: 211px; top: 368px; width: 962px; }
  .price-list--weed li { justify-content: space-between; }
  .price-list--hash { left: 34px; top: 1707px; width: 1000px; }
  .price-list--hash .price { width: 206px; }
  .skyline {
    position: absolute; left: 0; top: 2448px; width: 1200px; height: 208px;
    background: linear-gradient(180deg, #1e1e1e 0%, #121212 55%, var(--skyline) 100%);
  }
  .footer {
    position: absolute; left: 0; top: 2656px; width: 1200px; height: 224px;
    background: var(--panel);
  }
  .footer-title {
    position: absolute; left: 244px; width: 720px; top: 2698px;
    display: flex; justify-content: space-between;
    color: var(--white); font-size: 134px; line-height: 1;
  }
</style>
</head>
<body>
<main class="menu">
  <div class="leaf-decor leaf-decor--top" role="img" aria-label="Faint cannabis leaf decoration"></div>
  <div class="leaf-decor leaf-decor--left" role="img" aria-label="Faint cannabis leaf decoration"></div>
  <div class="leaf-decor leaf-decor--right" role="img" aria-label="Faint cannabis leaf decoration"></div>

  <div class="notice">
    <span>NO CIGARETTES</span>
    <svg viewBox="0 0 70 70" aria-label="No smoking">
      <circle cx="35" cy="35" r="29" fill="none" stroke="#fff" stroke-width="6"/>
      <rect x="15" y="33" width="34" height="8" fill="#fff"/>
      <rect x="51" y="33" width="5" height="8" fill="#fff"/>
      <line x1="15" y1="15" x2="55" y2="55" stroke="#fff" stroke-width="6"/>
    </svg>
  </div>

  <h1 class="heading heading--weed" style="margin:0;font-weight:400"><span>W</span><span>E</span><span>E</span><span>D</span></h1>
  <div class="tab--weed"></div>
  <div class="panel panel--weed"></div>
  <span class="unit unit--weed">p/g</span>
  <ul class="price-list price-list--weed">
    <li><span class="name">Oblivane</span><span class="price">€16</span></li>
    <li><span class="name">Cloudplum</span><span class="price">€14</span></li>
    <li><span class="name">Tide Runner</span><span class="price">€14</span></li>
    <li><span class="name">Quincefig</span><span class="price">€16</span></li>
    <li><span class="name">Mega Marsh</span><span class="price">€14</span></li>
    <li><span class="name">Grey Heron</span><span class="price">€14</span></li>
  </ul>

  <svg class="tab--hash" viewBox="0 0 270 130" aria-hidden="true">
    <polygon points="0,0 150,0 270,130 0,130" fill="#000"/>
  </svg>
  <h2 class="heading heading--hash" style="margin:0;font-weight:400"><span>H</span><span>A</span><span>S</span><span>H</span></h2>
  <div class="panel panel--hash"></div>
  <span class="unit unit--hash">p/g</span>
  <ul class="price-list price-list--hash">
    <li><span class="price">€12</span><span class="name">Tashar Amber</span></li>
    <li><span class="price">€11</span><span class="name">Pebble Frost</span></li>
    <li><span class="price">€14</span><span class="name">Lime Dunes</span></li>
    <li><span class="price">€10</span><span class="name">Ash Petal</span></li>
  </ul>

  <div class="skyline" role="img" aria-label="Amsterdam city skyline silhouette"></div>
  <div class="footer"></div>
  <div class="footer-title"><span>M</span><span>E</span><span>N</span><span>U</span></div>
</main>
</body>
</html>
```